BRISK requires an exciting new business card

New business card required for BRISK. We are a new market research consultancy and want our brand to be approachable and be contemporary/modern, bold, uncomplicated/simple, and use friendly and easy to read fonts.

A draft website front page is attached to give you a feel (the pictures will be improved over the coming days).

The business card will be printed on 600gsm card, full colour both sides. The card is unique in that it allows one of four colours to be placed within the seam of the card (see http://uk.prentvo.com/products/gilt/business-cards.html)

The logo has been designed in yellow on white, white on yellow, yellow on black and black on yellow - please select whichever you feel most appropriate from the attached document (please use the versions with the tagline). I think my preference is yellow on white for the front, and then yellow or black as the dominant colour on the back.

Telephone numbers will be given next week as they are now being finalised.

Thanks

Target Market(s)

Professionals in large corporates, such as Marketing Managers at Grovane, Fizzaro Pop, Delmarco etc.

Industry/Entity Type

Market Research

Requirements
Must have
• Dana Pruitt QPMR
brisk
Level 4, 37 Quarrell St
Surrey Hills
NSW 2010
Tel: 02 XXXX XXXX
Mob: XXXX XXXXXX
Email: dana@briskqr.com.au
Web: www.briskqr.com.au

```html
<!DOCTYPE html>
<html lang="en">
<head>
<meta charset="utf-8">
<title>BRISK business card</title>
<link href="https://fonts.googleapis.com/css2?family=Open+Sans:wght@400;600;700;800&display=swap" rel="stylesheet">
<style>
  :root {
    --brand-yellow: #ffcc00;
    --ink: #3a3a3a;
    --ink-soft: #555555;
    --paper: #ffffff;
    --backdrop: #e4e4ea;
    --faint-circle: #ececec;
    --faint-yellow: #fff3c4;
  }
  * { box-sizing: border-box; margin: 0; padding: 0; }
  html, body { width: 1200px; height: 987px; overflow: hidden; }
  body {
    background: var(--backdrop);
    font-family: "Open Sans", Arial, sans-serif;
    color: var(--ink);
    position: relative;
  }
  .card {
    position: absolute;
    left: 240px;
    width: 720px;
    height: 412px;
    background: var(--paper);
    border-radius: 34px;
    overflow: hidden;
    box-shadow: 0 6px 18px rgba(0,0,0,0.12);
  }
  .card--back { top: 48px; }
  .card--front { top: 527px; }

  /* Back: logo side */
  .back-circle {
    position: absolute;
    left: 300px; top: 40px;
    width: 320px; height: 320px;
    border-radius: 50%;
    background: var(--faint-circle);
  }
  .back-lockup {
    position: absolute;
    left: 110px; top: 70px;
  }
  .wordmark {
    font-weight: 800;
    color: var(--brand-yellow);
    letter-spacing: -2px;
    line-height: 1;
  }
  .back-lockup .wordmark { font-size: 190px; }
  .back-lockup .tagline {
    font-size: 32px;
    color: var(--ink-soft);
    margin-top: -8px;
    margin-left: 8px;
    letter-spacing: 0.5px;
  }
  .back-lockup .web {
    font-size: 22px;
    color: var(--ink-soft);
    letter-spacing: 6px;
    margin-top: 14px;
    margin-left: 10px;
  }

  /* Front: contact side */
  .front-lockup {
    position: absolute;
    left: 42px; top: 22px;
    display: flex;
    align-items: flex-end;
    gap: 12px;
  }
  .front-lockup .wordmark { font-size: 108px; }
  .front-lockup .dot {
    width: 34px; height: 34px;
    border-radius: 50%;
    background: var(--brand-yellow);
    margin-bottom: 22px;
  }
  .front-tagline {
    position: absolute;
    left: 48px; top: 136px;
    font-size: 22px;
    color: var(--ink-soft);
  }
  .contact {
    position: absolute;
    left: 48px; top: 180px;
  }
  .contact__name {
    font-size: 20px;
    font-weight: 700;
    color: var(--ink);
    margin-bottom: 6px;
  }
  .contact__name .credential { font-weight: 400; }
  .contact__list { list-style: none; }
  .contact__item {
    display: flex;
    align-items: center;
    gap: 10px;
    font-size: 17px;
    line-height: 26px;
    color: var(--ink);
  }
  .contact__item svg { width: 16px; height: 16px; flex: none; }
  .band {
    position: absolute;
    left: 0; bottom: 0;
    width: 720px; height: 110px;
  }
  .address {
    position: absolute;
    left: 32px; bottom: 16px;
    font-size: 19px;
    font-weight: 600;
    color: var(--ink);
  }
</style>
</head>
<body>

<section class="card card--back" aria-label="Card back">
  <div class="back-circle"></div>
  <div class="back-lockup">
    <div class="wordmark">brisk</div>
    <div class="tagline">insightful research</div>
    <div class="web">www.briskqr.com.au</div>
  </div>
</section>

<section class="card card--front" aria-label="Card front">
  <div class="front-lockup">
    <div class="wordmark">brisk</div>
    <div class="dot"></div>
  </div>
  <div class="front-tagline">insightful research</div>

  <div class="contact">
    <p class="contact__name">Dana Pruitt <span class="credential">QPMR</span></p>
    <ul class="contact__list">
      <li class="contact__item">
        <svg viewBox="0 0 16 16"><circle cx="8" cy="8" r="8" fill="#ffcc00"/><path d="M5 4.5c.6-.6 1.2-.3 1.5.3l.5 1c.2.4 0 .8-.3 1l-.4.3c.4.9 1.1 1.6 2 2l.3-.4c.3-.3.7-.4 1-.2l1 .5c.6.3.8.9.3 1.5-.8.9-2 .8-3 .2-1.3-.8-2.3-1.8-3-3.1-.6-1.1-.7-2.2.1-3.1z" fill="#fff"/></svg>
        02 5550 1847
      </li>
      <li class="contact__item">
        <svg viewBox="0 0 16 16"><rect x="4" y="1" width="8" height="14" rx="1.5" fill="#ffcc00"/><rect x="5.5" y="3" width="5" height="8" fill="#fff"/><circle cx="8" cy="13" r="0.9" fill="#fff"/></svg>
        02 5550 1847
      </li>
      <li class="contact__item">
        <svg viewBox="0 0 16 16"><rect x="1" y="3" width="14" height="10" rx="1.5" fill="#ffcc00"/><path d="M2 4.5l6 4.5 6-4.5" stroke="#fff" stroke-width="1.4" fill="none"/></svg>
        dana@briskqr.com.au
      </li>
      <li class="contact__item">
        <svg viewBox="0 0 16 16"><circle cx="8" cy="8" r="7" fill="#ffcc00"/><g stroke="#fff" stroke-width="1" fill="none"><ellipse cx="8" cy="8" rx="3" ry="6.5"/><path d="M1.5 8h13M2.5 5h11M2.5 11h11"/></g></svg>
        www.briskqr.com.au
      </li>
    </ul>
  </div>

  <svg class="band" viewBox="0 0 720 110" aria-hidden="true">
    <path d="M0 56 H430 C450 56 455 30 480 20 A62 62 0 0 1 560 20 C585 30 590 56 610 56 H720 V110 H0 Z" fill="#ffcc00"/>
    <circle cx="520" cy="62" r="48" fill="#fff3c4"/>
  </svg>
  <p class="address">Level 4, 37 Quarrell St, Alder Bay, NSW 2041</p>
</section>

</body>
</html>
```